Dalvick's Business Card

I need some designs for a new business card including the new logo attached. An old example of our business card is also attached to show all the data that should be included on the new design.
**I added some more examples someone had mocked up**

Contact Information for Business Card

Should include all info on other examples uploaded.

```html
<!DOCTYPE html>
<html lang="en">
<head>
<meta charset="utf-8">
<title>Dalvick's Business Card</title>
<link rel="stylesheet" href="https://fonts.googleapis.com/css2?family=Montserrat:wght@400;500;700&display=swap">
<style>
  :root {
    --blue: #1565b0;
    --red: #e3262c;
    --ink: #222222;
    --paper: #ffffff;
    --backdrop: #7a6a55;
    --ghost: #eef2f8;
  }
  html, body {
    margin: 0;
    padding: 0;
    width: 900px;
    height: 1200px;
    overflow: hidden;
    background: var(--backdrop);
    font-family: "Montserrat", sans-serif;
  }
  .card {
    position: absolute;
    left: 80px;
    width: 742px;
    height: 440px;
    background: var(--paper);
    border-radius: 32px;
    overflow: hidden;
    box-shadow: 0 10px 18px rgba(0,0,0,0.45);
  }
  .card--front { top: 132px; }
  .card--back { top: 638px; }
  .ghost-mark {
    position: absolute;
    right: -60px;
    top: 40px;
    width: 300px;
    height: 300px;
    border-radius: 50%;
    background: var(--ghost);
  }
  .brand {
    position: absolute;
    display: flex;
    align-items: center;
    gap: 16px;
    color: var(--blue);
    font-weight: 700;
    line-height: 1;
  }
  .brand__dot {
    border-radius: 50%;
    background: var(--red);
  }
  .card--front .brand { left: 44px; top: 68px; font-size: 64px; }
  .card--front .brand__dot { width: 48px; height: 48px; }
  .card--back .brand { left: 0; right: 0; top: 185px; justify-content: center; font-size: 74px; }
  .card--back .brand__dot { width: 56px; height: 56px; }
  .person {
    position: absolute;
    left: 42px;
    top: 286px;
    margin: 0;
    font-size: 27px;
    font-weight: 700;
    color: var(--blue);
  }
  .rule {
    position: absolute;
    left: 42px;
    top: 321px;
    width: 655px;
    height: 2px;
    background: var(--blue);
  }
  .contact {
    position: absolute;
    left: 42px;
    top: 335px;
    margin: 0;
    padding: 0;
    list-style: none;
    font-size: 17px;
    color: var(--ink);
  }
  .contact li {
    display: flex;
    align-items: center;
    gap: 12px;
    height: 24px;
  }
  .contact svg { width: 16px; height: 14px; }
  .credential {
    position: absolute;
    right: 45px;
    top: 355px;
    font-size: 15px;
    font-weight: 500;
    color: var(--ink);
  }
  .bands {
    position: absolute;
    left: 0;
    bottom: 0;
    width: 742px;
    height: 60px;
  }
  .tagline {
    position: absolute;
    right: 24px;
    bottom: 16px;
    font-size: 15.5px;
    font-weight: 500;
    color: var(--paper);
  }
  .base-band {
    position: absolute;
    left: 0;
    bottom: 0;
    width: 100%;
    height: 15px;
    background: var(--blue);
  }
</style>
</head>
<body>
  <section class="card card--front">
    <div class="ghost-mark" aria-hidden="true"></div>
    <div class="brand"><span class="brand__dot"></span>Dalvick's</div>
    <h1 class="person">Mark Dalvick</h1>
    <div class="rule"></div>
    <ul class="contact">
      <li>
        <svg viewBox="0 0 16 14" aria-hidden="true"><path fill="#e3262c" d="M2 4c0-2 3-3 6-3s6 1 6 3v1h-3V4H5v1H2zM4 6h8l2 7H2z"/></svg>
        555.014.2290
      </li>
      <li>
        <svg viewBox="0 0 16 14" aria-hidden="true"><rect x="1" y="2" width="14" height="10" fill="#1565b0"/><path d="M1 2l7 6 7-6" fill="none" stroke="#fff" stroke-width="1.3"/></svg>
        service@dalvickhvac.com
      </li>
    </ul>
    <div class="credential">LICENSED &amp; INSURED</div>
    <svg class="bands" viewBox="0 0 742 60" aria-hidden="true">
      <path fill="var(--red)" d="M0 0H405a8 8 0 0 1 0 14H0z"/>
      <path fill="var(--blue)" d="M0 20H410C440 20 440 -10 470 -10H742V60H0z"/>
    </svg>
    <div class="tagline">FAMILY OWNED &amp; OPERATED</div>
  </section>

  <section class="card card--back">
    <div class="ghost-mark" aria-hidden="true"></div>
    <div class="brand"><span class="brand__dot"></span>Dalvick's</div>
    <div class="base-band"></div>
  </section>
</body>
</html>
```